Upscale square business card for photographer

I need the logo I already own designed into a card that features a photo on one side and text on the other. I want a very upscale approach that can be printed on thick paper - maybe even letterpress.

Target Market(s)

Designers, artists, editors

Industry/Entity Type

Business

Contact Information for Business Card

Should be square and feature the text below

Font styles to use
Serif
Sans Serif

Requirements
Must have
• Following contact info:
• Dale Wickham
• 253-417-6924
• dale@dalewickham-example.com
Nice to have
• Mailing address
• 2967 Larkmere Ave. NW #158
• Alder Cove, OR 97491
Should not have
• Should be monochrome - no color

```html
<!DOCTYPE html>
<html lang="en">
<head>
<meta charset="utf-8">
<title>Dale Wickham — Square Business Card</title>
<link href="https://fonts.googleapis.com/css2?family=Oswald:wght@400&family=Open+Sans:wght@400&display=swap" rel="stylesheet">
<style>
  :root {
    --backdrop: #8c8c8c;
    --card-dark: #2b2a2a;
    --card-light: #ffffff;
    --ink-dark: #1c1c1c;
    --ink-body: #3a3a3a;
    --ink-light: #ffffff;
    --photo-deep: #1f1e1e;
    --photo-mid: #4a4848;
    --photo-glow: #8d8a8a;
  }
  * { margin: 0; padding: 0; box-sizing: border-box; }
  html, body {
    width: 1200px;
    height: 1200px;
    overflow: hidden;
  }
  body {
    background: var(--backdrop);
    display: flex;
    align-items: center;
    justify-content: center;
    gap: 60px;
    font-family: "Open Sans", Arial, sans-serif;
  }
  .card {
    width: 520px;
    height: 520px;
    position: relative;
    box-shadow: 0 6px 18px rgba(0,0,0,0.25);
  }
  /* Front: photo side */
  .card--front {
    background: var(--card-dark);
    overflow: hidden;
  }
  .card__photo {
    position: absolute;
    inset: 0;
    background:
      radial-gradient(ellipse 38% 34% at 46% 38%, var(--photo-glow) 0%, var(--photo-mid) 45%, transparent 75%),
      linear-gradient(180deg, var(--photo-deep) 0%, var(--card-dark) 70%, #161515 100%);
  }
  .card__wordmark {
    position: absolute;
    left: 0;
    right: 0;
    top: 228px;
    text-align: center;
    font-family: "Oswald", "Arial Narrow", sans-serif;
    font-weight: 400;
    font-size: 40px;
    letter-spacing: 0.22em;
    padding-left: 0.22em;
    text-transform: uppercase;
    color: var(--ink-light);
  }
  /* Back: contact side */
  .card--back {
    background: var(--card-light);
    display: flex;
    flex-direction: column;
    align-items: center;
    justify-content: center;
    text-align: center;
  }
  .contact__name {
    font-family: "Oswald", "Arial Narrow", sans-serif;
    font-weight: 400;
    font-size: 34px;
    letter-spacing: 0.22em;
    padding-left: 0.22em;
    text-transform: uppercase;
    color: var(--ink-dark);
    margin-bottom: 26px;
  }
  .contact__icons {
    display: flex;
    gap: 6px;
    margin-bottom: 8px;
  }
  .contact__icons svg {
    width: 22px;
    height: 22px;
  }
  .contact__address,
  .contact__line {
    font-size: 15px;
    line-height: 1.35;
    color: var(--ink-body);
  }
  .contact__address { margin-bottom: 6px; }
</style>
</head>
<body>
  <section class="card card--front">
    <div class="card__photo" role="img" aria-label="Black and white photograph of a wading bird with spread feathers standing in dark water"></div>
    <div class="card__wordmark">Dale Wickham</div>
  </section>

  <section class="card card--back">
    <h1 class="contact__name">Dale Wickham</h1>
    <div class="contact__icons">
      <svg viewBox="0 0 22 22" aria-label="Address">
        <circle cx="11" cy="11" r="9.5" fill="none" stroke="#1c1c1c" stroke-width="1.5"/>
        <path d="M11 5.5a3.5 3.5 0 0 0-3.5 3.5c0 2.6 3.5 6.5 3.5 6.5s3.5-3.9 3.5-6.5A3.5 3.5 0 0 0 11 5.5z" fill="#1c1c1c"/>
        <circle cx="11" cy="9" r="1.3" fill="#fff"/>
      </svg>
      <svg viewBox="0 0 22 22" aria-label="Phone">
        <circle cx="11" cy="11" r="9.5" fill="none" stroke="#1c1c1c" stroke-width="1.5"/>
        <path d="M8 6.2l1.6-.4 1 2.4-1 .8a6 6 0 0 0 2.6 2.6l.8-1 2.4 1-.4 1.6c-.2.6-.8 1-1.4.9A7.5 7.5 0 0 1 7.1 7.6c-.1-.6.3-1.2.9-1.4z" fill="#1c1c1c"/>
      </svg>
      <svg viewBox="0 0 22 22" aria-label="Email">
        <circle cx="11" cy="11" r="9.5" fill="none" stroke="#1c1c1c" stroke-width="1.5"/>
        <rect x="6" y="7.5" width="10" height="7" rx="1" fill="#1c1c1c"/>
        <path d="M6.5 8l4.5 3.5L15.5 8" fill="none" stroke="#fff" stroke-width="1"/>
      </svg>
    </div>
    <p class="contact__address">2967 Larkmere Ave. NW #158,<br>Alder Cove, OR 97491</p>
    <p class="contact__line">253-417-6924</p>
    <p class="contact__line">dale@dalewickham-example.com</p>
  </section>
</body>
</html>
```